Catalogue Design Project

We need a catalog design for a new private university called Redwell Institute Bayshore (see website www.rwi-bs.org). The catalog should be about 30 pages maximum and will include items such as General Information, Academic schedule, department descriptions, program descriptions, course descriptions, school policies, student services, admissions, San diego Lifestyle, etc.
I will provide the text but I need a professional design with regard to page layouts. I have provided some examples.
Ok, i posted the catalog content, just missing course descriptions.
Target Market(s)
Young Professionals, Foreign Students
Industry/Entity Type
University
Look and feel
Each slider illustrates characteristics of the customer's brand and the style your logo design should communicate.

```html
<!DOCTYPE html>
<html lang="en">
<head>
<meta charset="utf-8">
<title>Academic Programs – Starting Your Own Business Certificate</title>
<link href="https://fonts.googleapis.com/css2?family=Carlito:wght@400;700&display=swap" rel="stylesheet">
<style>
  :root {
    --navy: #1f4e82;
    --navy-deep: #173e6b;
    --steel: #5b84b1;
    --rule: #9fb4cc;
    --ornament-grey: #b4b4b4;
    --ornament-blue: #3d6796;
    --ink: #141414;
    --heading-ink: #1a1a1a;
    --footer-ink: #8a8a8a;
    --paper: #ffffff;
    --sepia-light: #f5efe4;
    --sepia-mid: #dccdb3;
  }
  * { margin: 0; padding: 0; box-sizing: border-box; }
  html, body { width: 927px; height: 1200px; overflow: hidden; background: var(--paper); }
  .page {
    position: relative;
    width: 927px;
    height: 1200px;
    background: var(--paper);
    font-family: "Carlito", sans-serif;
    color: var(--ink);
  }
  .header-photo {
    position: absolute;
    top: 0; right: 0;
    width: 420px; height: 150px;
    background: linear-gradient(to right, rgba(255,255,255,1) 0%, rgba(245,239,228,0.7) 30%, var(--sepia-mid) 70%, var(--sepia-light) 100%);
    -webkit-mask-image: linear-gradient(to bottom, #000 55%, transparent 100%);
            mask-image: linear-gradient(to bottom, #000 55%, transparent 100%);
  }
  .brand-ornament {
    position: absolute;
    left: 58px; top: 58px;
    width: 152px; height: 32px;
    border-radius: 10px;
    background: linear-gradient(to right, var(--ornament-grey) 0%, #c4c4c4 60%, var(--ornament-blue) 100%);
    opacity: 0.55;
  }
  .section-title {
    position: absolute;
    left: 303px; top: 96px;
    width: 318px;
    text-align: center;
    font-size: 31px;
    line-height: 36px;
    color: var(--heading-ink);
  }
  .header-rule {
    position: absolute;
    left: 0; right: 0; top: 150px;
    height: 2px;
    background: var(--rule);
  }
  .header-bar {
    position: absolute;
    left: 303px; top: 133px;
    width: 318px; height: 17px;
    background: var(--navy);
  }
  .category-tab {
    position: absolute;
    left: 0; top: 178px;
    width: 427px; height: 42px;
    background: linear-gradient(to bottom, var(--steel) 0%, var(--navy) 45%, var(--navy-deep) 100%);
    border-radius: 0 12px 12px 0;
    box-shadow: 2px 2px 3px rgba(0,0,0,0.35);
    color: #fff;
    font-size: 31px;
    line-height: 42px;
    padding-left: 62px;
  }
  .tab-rule {
    position: absolute;
    left: 427px; right: 0; top: 218px;
    height: 1px;
    background: var(--rule);
  }
  .program {
    position: absolute;
    left: 80px; top: 246px;
    width: 803px;
    font-size: 19.7px;
    line-height: 28px;
  }
  .program-title {
    text-align: center;
    font-size: 24px;
    font-weight: 700;
    line-height: 30px;
    color: var(--heading-ink);
  }
  .program-text { text-align: justify; }
  .program-text + .program-text { margin-top: 28px; }
  .meta strong { font-weight: 700; }
  .meta-label { text-decoration: underline; }
  .course-block { margin-top: 28px; }
  .footer-rule {
    position: absolute;
    left: 0; right: 0; top: 1155px;
    height: 2px;
    background: var(--rule);
  }
  .footer-mark {
    position: absolute;
    right: 38px; top: 1170px;
    font-size: 14px;
    color: var(--footer-ink);
    letter-spacing: 0.4px;
  }
</style>
</head>
<body>
<div class="page">
  <div class="header-photo" role="img" aria-label="Softly faded photograph of an open antique book"></div>
  <div class="brand-ornament" role="img" aria-label="Decorative cluster of grey and blue dots"></div>

  <div class="section-title">ACADEMIC PROGRAMS</div>
  <div class="header-rule"></div>
  <div class="header-bar"></div>

  <div class="category-tab">CERTIFICATE PROGRAMS</div>
  <div class="tab-rule"></div>

  <article class="program">
    <h1 class="program-title">Starting Your Own Business Certificate</h1>
    <p class="program-text">Staring your own business should be the ultimate goal for any entrepreneur or anyone really wanting to get ahead in life. &nbsp;This certificate prepares future business owners for today's market and what's required to get a successful product out there. &nbsp;The certificate covers many of the steps needed to get ready, including the initial decision-making process related to deciding the type of business: franchise, independent, service, manufacturing, retail, online, consumer, or business-to-business. &nbsp;Also mentioned are start-up requirements such as selecting the type of corporation to form, applying to receive articles of incorporation, opening a business bank account, purchasing a business owner insurance policy, worker's compensation, applying for a business license, creating employment agreements, writing company policies and many others.</p>
    <p class="program-text">Subsequently, the course heavily focuses on researching ideas and ensuring that everything is well investigated before making the product or service available. &nbsp;Putting a product out on the market too quickly can squander precious resources and potentially be penalized by being positioned incorrectly in the marketplace. &nbsp;It's far better to be methodical and diligently research a prospect not just with respect to the product itself, but also to competition, existing substitutes, viability, and demand. &nbsp;The best method for covering all of ones bases is in the production of a business plan. &nbsp;It forces answers to all of the questions that must be asked in order to really find out if a product is going to be successful or not. &nbsp;Questions such as what the purpose of the business is, who the customers are, what problem does the product solve, what is the competitive advantage, what are the projections for future years, and what the best methods to pricing, positioning and marketing the product are.</p>
    <div class="meta">
      <div><strong>Hours:</strong> 6 hours per week</div>
      <div><strong>Length:</strong> 8 weeks per course</div>
    </div>
    <div class="course-block">
      <div class="meta-label">Course:</div>
      <div>BUS 600 Starting Your Own Business</div>
    </div>
    <div class="course-block">
      <div class="meta-label">Learning Outcome:</div>
      <div>Open a legitimate company with a clear idea for achieving profit, create a logo and website, secure a location, conduct in-depth research, and market a product.</div>
    </div>
  </article>

  <div class="footer-rule"></div>
  <div class="footer-mark">10::: REDWELL INSTITUTE</div>
</div>
</body>
</html>
```